Brindle Water - 500ml

to create a water bottle packaging similar to L'onde Claire design. Bottle should be blue similar to PURE FLOW but change the design/logo to Brindle. Wording should be similar just different design and logo. Thanks.

Colors
0054AA
0677BA
7BADD7
CADEEF
E8F1F8

Requirements
Must have
• Bottle must not be in plastic bottles. They are made in a carton instead - see PURE FLOW for reference.

```html
<!DOCTYPE html>
<html lang="en">
<head>
<meta charset="UTF-8">
<title>Brindle Water – 500ml Carton Front Panel</title>
<link href="https://fonts.googleapis.com/css2?family=Montserrat:wght@500;600;700&family=Barlow+Condensed:wght@500&display=swap" rel="stylesheet">
<style>
  :root {
    --backdrop: #e4e4e4;
    --carton-light: #7dbbe2;
    --carton-deep: #5ea3d2;
    --navy: #3a4f8c;
    --ink-light: #e8f1f8;
    --wave-bright: #1e94dc;
    --wave-mid: #5da7da;
    --wave-pale: #a8cbe0;
  }
  * { margin: 0; padding: 0; box-sizing: border-box; }
  html, body {
    width: 1200px; height: 1200px; overflow: hidden;
    background: var(--backdrop);
  }
  .canvas {
    position: relative; width: 1200px; height: 1200px;
  }
  .carton-front {
    position: absolute; left: 393px; top: 40px;
    width: 414px; height: 1120px;
    background: linear-gradient(90deg, var(--carton-deep) 0%, var(--carton-light) 30%, var(--carton-light) 70%, var(--carton-deep) 100%);
    font-family: "Montserrat", sans-serif;
    text-align: center;
  }
  .brand-name {
    position: absolute; left: 0; right: 0; top: 190px;
    font-weight: 700; font-size: 78px; letter-spacing: -1px;
    color: var(--navy);
  }
  .brand-tagline {
    position: absolute; left: 0; right: 0; top: 302px;
    font-family: "Barlow Condensed", sans-serif; font-weight: 500;
    font-size: 13px; letter-spacing: 1.3px; color: var(--navy);
  }
  .product-title {
    position: absolute; left: 0; right: 0; top: 486px;
    font-weight: 600; font-size: 32px; line-height: 40px;
    color: var(--ink-light);
  }
  .product-claim {
    position: absolute; left: 0; right: 0; top: 746px;
    font-weight: 600; font-size: 14.5px; line-height: 18px;
    color: var(--ink-light);
  }
  .wave-decoration {
    position: absolute; left: 0; top: 806px; width: 414px; height: 130px;
    background: linear-gradient(180deg, var(--wave-bright) 0%, var(--wave-mid) 60%, var(--wave-pale) 100%);
  }
  .volume {
    position: absolute; left: 0; right: 0; top: 990px;
    font-weight: 500; font-size: 18px; color: var(--navy);
  }
</style>
</head>
<body>
<div class="canvas">
  <section class="carton-front">
    <h1 class="brand-name">Brindle</h1>
    <p class="brand-tagline">BEVERAGES | EST CIRCA 1860</p>

    <p class="product-title">100%<br>Spring Water</p>

    <p class="product-claim">Sustainably sourced water<br>in a plant-based carton</p>

    <div class="wave-decoration" role="img" aria-label="Decorative band of layered water waves in bright, mid and pale blues"></div>

    <p class="volume">500ml ℮</p>
  </section>
</div>
</body>
</html>
```